New Alcoholic Spiked Seltzer Line

We need a can design for a line of low calorie alcoholic seltzer. This product is a sparkling water and vodka drink with no sugar added in a slim 12 oz can.

This is a lighter, healthier, alternative to the sugary ready-to-drinks on the market. The product contains only 3 ingredients: Vodka, Water and Natural Flavors. It has only 100 calories but still has 5% alcohol, so you don't need to sacrifice alcohol to cut calories.

This product also does not contain any preservatives.

We want this design to communicate the following objectives to the consumer and in this order:

1. Appetizing product
2.Low calorie
3.Communicate the type of beverage (Spiked Seltzer)

The brand name of the product is VELKA.

The flavor of the product needed to be used for the design is Mango-Orange.

Comparable products are:

www.brindlefizzworks.example/
https://www.quorvabubbles.example
https://pelnavo.example/

The designs should not infringe or copy the creative directions of the products mentionned above. They are only given so that you can better understand the type of product we are developing.

Target Market(s)

Young Professional women between the ages of 25 and 44

Industry/Entity Type

Product

Colors

Designer to choose colors to be used in the design.

Requirements
Must have
• Design extendibility, meaning it can be adapted for other flavors.
• This is a new category in the market we are targeting, so consumers must easily be able to identify what type of product this is.

```html
<!DOCTYPE html>
<html lang="en">
<head>
<meta charset="utf-8">
<title>VELKA Spiked Seltzer – Mango-Orange Can Label</title>
<link rel="stylesheet" href="https://fonts.googleapis.com/css2?family=Jost:wght@300;400&family=Antonio:wght@100&display=swap">
<style>
  :root {
    --bg: #e4e6e8;
    --label-white: #f7f8f9;
    --ray-orange: #f08a4b;
    --peach-light: #fbe3cf;
    --peach-mid: #f7c9a3;
    --orange: #f0955a;
    --orange-deep: #e9813f;
    --plum: #6b2348;
    --ink: #2a2626;
  }
  * { box-sizing: border-box; margin: 0; padding: 0; }
  html, body {
    width: 1200px;
    height: 800px;
    overflow: hidden;
    background: var(--bg);
  }
  .canvas {
    position: relative;
    width: 1200px;
    height: 800px;
  }
  .can-label {
    position: absolute;
    left: 440px;
    top: 60px;
    width: 320px;
    height: 680px;
    background: var(--label-white);
    overflow: hidden;
    box-shadow: 0 10px 30px rgba(0,0,0,0.08);
  }
  .label-bands {
    position: absolute;
    inset: 0;
    width: 320px;
    height: 680px;
  }
  .sunburst {
    position: absolute;
    left: 10px;
    top: 110px;
    width: 300px;
    height: 400px;
    border-radius: 50%;
    background: radial-gradient(ellipse at center, rgba(240,138,75,0.55) 0%, rgba(240,138,75,0.25) 35%, rgba(240,138,75,0) 70%);
  }
  .calories {
    position: absolute;
    top: 72px;
    left: 0;
    width: 100%;
    text-align: center;
    font-family: 'Jost', sans-serif;
    font-weight: 300;
    font-size: 13px;
    letter-spacing: 2.5px;
    color: var(--ink);
  }
  .brand-name {
    position: absolute;
    top: 262px;
    left: 0;
    width: 100%;
    text-align: center;
    font-family: 'Jost', sans-serif;
    font-weight: 400;
    font-size: 46px;
    letter-spacing: 4px;
    color: var(--plum);
  }
  .flavor {
    position: absolute;
    top: 524px;
    left: 0;
    width: 100%;
    text-align: center;
    font-family: 'Antonio', sans-serif;
    font-weight: 100;
    font-size: 44px;
    line-height: 1;
    color: var(--ink);
  }
  .category {
    position: absolute;
    top: 584px;
    left: 0;
    width: 100%;
    text-align: center;
    font-family: 'Jost', sans-serif;
    font-weight: 400;
    font-size: 14px;
    letter-spacing: 3px;
    color: var(--ink);
  }
  .facts {
    position: absolute;
    top: 624px;
    left: 0;
    width: 100%;
    text-align: center;
    font-family: 'Jost', sans-serif;
    font-weight: 300;
    font-size: 12.5px;
    letter-spacing: 2px;
    color: var(--ink);
    word-spacing: 4px;
  }
</style>
</head>
<body>
  <main class="canvas">
    <section class="can-label">
      <svg class="label-bands" viewBox="0 0 320 680" aria-hidden="true">
        <path fill="var(--peach-light)" d="M0 440 C 60 425, 110 440, 150 425 C 200 405, 250 400, 320 415 L320 680 L0 680 Z"/>
        <path fill="var(--peach-mid)" d="M0 520 C 50 505, 100 515, 150 500 C 200 485, 260 485, 320 500 L320 680 L0 680 Z"/>
        <path fill="var(--orange)" d="M0 600 C 40 590, 90 610, 140 595 C 190 580, 230 560, 270 560 C 295 560, 310 550, 320 545 L320 680 L0 680 Z"/>
        <path fill="var(--orange-deep)" opacity="0.5" d="M0 650 C 80 640, 200 650, 320 640 L320 680 L0 680 Z"/>
      </svg>
      <div class="sunburst" role="img" aria-label="Radiating orange sunburst rays around the brand name"></div>
      <p class="calories">100 CALORIES</p>
      <h1 class="brand-name">VELKA</h1>
      <p class="flavor">MANGO-ORANGE</p>
      <p class="category">SPIKED SELTZER</p>
      <p class="facts">NO SUGAR 5% ALCOHOL</p>
    </section>
  </main>
</body>
</html>
```